VOMRA Pty Ltd Business Card

Looking for a simple yet eye-catching double-sided business card design using my company logo on one side and contact details on the other.

Target Market(s)

Government

Industry/Entity Type

Communication Systems Engineering

Contact Information for Business Card

VOMRA Pty Ltd

Requirements
Nice to have
• Would be great to have a QR code so details can be scanned into contacts

```html
<!DOCTYPE html>
<html lang="en">
<head>
<meta charset="utf-8">
<title>VOMRA Pty Ltd Business Card</title>
<link rel="stylesheet" href="https://fonts.googleapis.com/css2?family=Montserrat:wght@400;500;800&display=swap">
<style>
  :root {
    --ink: #35424a;
    --black: #0d0d0d;
    --paper: #ffffff;
    --backdrop: #e9e8e6;
    --shadow: rgba(0, 0, 0, 0.18);
  }
  * { margin: 0; padding: 0; box-sizing: border-box; }
  html, body {
    width: 1200px; height: 960px; overflow: hidden;
    background: var(--backdrop);
    font-family: "Montserrat", Arial, sans-serif;
    color: var(--ink);
  }
  .sheet {
    position: relative; width: 1200px; height: 960px;
  }
  .card {
    position: absolute; left: 240px;
    width: 720px; height: 412px;
    background: var(--paper);
    border-radius: 34px;
    overflow: hidden;
    box-shadow: 0 14px 34px var(--shadow);
  }
  .card--front { top: 44px; }
  .card--back { top: 502px; }

  /* Brand lockup */
  .brand {
    position: absolute; display: flex; align-items: center;
  }
  .brand__dot {
    border: 3px solid var(--ink); border-radius: 50%;
  }
  .brand__name {
    font-weight: 800; color: var(--ink); letter-spacing: 0.02em; line-height: 1;
  }
  .card--front .brand { left: 0; right: 0; top: 0; bottom: 0; justify-content: center; gap: 34px; }
  .card--front .brand__dot { width: 86px; height: 86px; }
  .card--front .brand__name { font-size: 112px; }

  .card--back .brand { left: 70px; top: 150px; gap: 18px; }
  .card--back .brand__dot { width: 50px; height: 50px; border-width: 2px; }
  .card--back .brand__name { font-size: 54px; }

  .divider {
    position: absolute; left: 372px; top: 70px;
    width: 1.5px; height: 220px; background: var(--ink);
  }

  .contact {
    position: absolute; left: 394px; top: 66px; width: 310px;
  }
  .contact__name {
    font-weight: 800; font-size: 25px; letter-spacing: 0.01em; line-height: 1.05;
  }
  .contact__role {
    font-weight: 400; font-size: 17px; margin-top: 2px;
  }
  .contact__list {
    list-style: none; margin-top: 20px;
  }
  .contact__item {
    display: flex; align-items: center; gap: 8px;
    font-size: 15.5px; line-height: 1.45;
  }
  .contact__icon { width: 14px; height: 14px; flex: none; fill: var(--ink); }
  .contact__address {
    font-style: normal; font-size: 15.5px; line-height: 1.35; margin-top: 16px;
  }

  .band {
    position: absolute; left: 0; top: 0; width: 720px; height: 412px;
  }
  .band__dark { fill: var(--ink); }
  .band__stripe { fill: var(--black); }
</style>
</head>
<body>
<main class="sheet">

  <section class="card card--front" aria-label="Card front">
    <div class="brand">
      <span class="brand__dot" aria-hidden="true"></span>
      <span class="brand__name">VOMRA</span>
    </div>
  </section>

  <section class="card card--back" aria-label="Card back">
    <svg class="band" viewBox="0 0 720 412" aria-hidden="true">
      <path class="band__dark" d="M556 300 H720 V412 H0 V394 H532 L556 364 Z"/>
      <path class="band__stripe" d="M0 378 H524 L549 346 L553 354 L530 386 H0 Z"/>
    </svg>

    <div class="brand">
      <span class="brand__dot" aria-hidden="true"></span>
      <span class="brand__name">VOMRA</span>
    </div>

    <div class="divider" aria-hidden="true"></div>

    <div class="contact">
      <h1 class="contact__name">DANIEL HARTLEY</h1>
      <p class="contact__role">Managing Director</p>
      <ul class="contact__list">
        <li class="contact__item">
          <svg class="contact__icon" viewBox="0 0 24 24" aria-hidden="true"><path d="M6.6 10.8a15.1 15.1 0 0 0 6.6 6.6l2.2-2.2c.3-.3.7-.4 1-.2 1.1.4 2.3.6 3.6.6.6 0 1 .4 1 1V20c0 .6-.4 1-1 1A17 17 0 0 1 3 4c0-.6.4-1 1-1h3.5c.6 0 1 .4 1 1 0 1.3.2 2.5.6 3.6.1.3 0 .7-.2 1z"/></svg>
          <span>02 5550 1842</span>
        </li>
        <li class="contact__item">
          <svg class="contact__icon" viewBox="0 0 24 24" aria-hidden="true"><path d="M2 5h20v14H2z M2 5l10 8 10-8" fill="none" stroke="currentColor" stroke-width="0"/><path d="M2 5h20v2l-10 7L2 7z M2 9l10 7 10-7v10H2z"/></svg>
          <span>admin@vomra.com.au</span>
        </li>
        <li class="contact__item">
          <svg class="contact__icon" viewBox="0 0 24 24" aria-hidden="true"><circle cx="12" cy="12" r="10"/><path d="M2 12h20M12 2c3 3 3 17 0 20M12 2c-3 3-3 17 0 20" stroke="#fff" stroke-width="1.4" fill="none"/></svg>
          <span>www.vomra.com.au</span>
        </li>
      </ul>
      <address class="contact__address">14-16 Harbour Lane Redfern<br>NSW 2016 Australia</address>
    </div>
  </section>

</main>
</body>
</html>
```